Polish brewery needs BEER LABEL design for WEDDINGS

We need beer label design for weddings. Our brewery is located on South of Poland and it is called Warsztat Kominek [PL]/Workshop Hearth [ENG]. We feel strong connection to mountains and we use water from the mountain in our vicinity.
Regarding beer style it is India Pale Ale so beer is bitter and aromatic because of high addition of hops. Label design has to be modern and simple. We would prefer bright and cream colors.
We need to have opportunity to edit data which are on the label so we will need to get appropriate files.
In attached files you can find all details. If any additional information will be required please do not hesitate and contact with me.

Target Market(s)

Weddings

Font styles to use
Sans Serif
Script

Colors
ffffff

Requirements
Must have
• Information listed in documents in attached files
Nice to have
• Some nice graphics
Bright and cream colors.
Should not have
• -

```html
<!DOCTYPE html>
<html lang="pl">
<head>
<meta charset="utf-8">
<title>Wedding IPA Label – Warsztat Kominek</title>
<link href="https://fonts.googleapis.com/css2?family=Great+Vibes&family=Montserrat:ital,wght@0,400;0,500;0,600;0,700;1,400&display=swap" rel="stylesheet">
<style>
  :root {
    --page: #ffffff;
    --cream: #f3e4d9;
    --cream-deep: #e9d3c4;
    --ink: #231f20;
    --brown: #6a3a30;
    --brown-soft: #8a5a4e;
    --copper: #d98a6c;
    --gold: #b08a3e;
    --leaf: #d9bfb0;
  }
  * { box-sizing: border-box; margin: 0; padding: 0; }
  html, body { width: 927px; height: 1200px; overflow: hidden; background: var(--page); }
  body { font-family: "Montserrat", sans-serif; color: var(--ink); position: relative; }

  .label {
    position: absolute; left: 13px; top: 400px;
    width: 900px; height: 400px;
    background: var(--cream);
    display: flex;
  }
  .panel { position: relative; width: 300px; height: 400px; }
  .panel + .panel { border-left: 1px solid var(--ink); }

  /* Back-left panel */
  .ingredients {
    position: absolute; left: 13px; top: 18px; width: 273px; height: 83px;
    background: var(--ink); color: #fff; border-radius: 4px; text-align: center;
  }
  .ingredients h2 { font-size: 15px; font-weight: 700; letter-spacing: 1px; margin-top: 7px; }
  .ingredients .rule { display: block; margin: 4px auto 4px; }
  .ingredients p { font-size: 12px; line-height: 15px; }

  .facts { position: absolute; left: 26px; top: 122px; width: 260px; }
  .fact { margin-bottom: 12px; }
  .fact h3 { font-size: 14.5px; font-weight: 600; letter-spacing: .5px; line-height: 18px; }
  .fact p { font-size: 13px; line-height: 16px; letter-spacing: .4px; }

  .brewery {
    position: absolute; left: 31px; top: 308px; width: 221px; height: 74px;
    border: 2px solid var(--ink); padding: 7px 10px;
  }
  .brewery-name { font-size: 14px; font-weight: 500; color: var(--gold); text-transform: uppercase; display: flex; align-items: center; gap: 6px; }
  .brewery-name .mark { width: 8px; height: 8px; background: var(--gold); }
  .brewery address { font-style: normal; font-size: 7.5px; font-weight: 600; line-height: 11px; margin-top: 5px; }

  /* Front panel */
  .leaves { position: absolute; background: var(--leaf); opacity: .55; border-radius: 40px; }
  .leaves.top { right: 0; top: 0; width: 118px; height: 48px; border-radius: 0 0 0 48px; }
  .leaves.side { left: 0; top: 35px; width: 22px; height: 100px; border-radius: 0 30px 30px 0; }
  .sprig { position: absolute; background: var(--ink); opacity: .7; border-radius: 6px; }
  .sprig.a { left: 263px; top: 85px; width: 10px; height: 58px; }
  .sprig.b { left: 14px; top: 233px; width: 10px; height: 60px; }
  .sprig.c { left: 274px; top: 343px; width: 8px; height: 35px; }

  .names { position: absolute; left: 0; top: 18px; width: 300px; font-family: "Great Vibes", cursive; color: var(--brown); }
  .names .first { position: absolute; left: 40px; top: 0; font-size: 68px; line-height: 80px; }
  .names .and { position: absolute; left: 124px; top: 66px; font-size: 28px; line-height: 34px; }
  .names .second { position: absolute; left: 70px; top: 94px; font-size: 68px; line-height: 80px; }

  .date { position: absolute; top: 228px; width: 300px; text-align: center; font-size: 13px; letter-spacing: 3px; }
  .short-rule { position: absolute; top: 257px; left: 120px; width: 60px; height: 1px; background: var(--copper); }
  .blurb { position: absolute; top: 276px; left: 40px; width: 220px; text-align: center; font-size: 8.5px; font-style: italic; line-height: 11px; color: #3b3436; }
  .ornament-rule { position: absolute; top: 338px; left: 42px; }
  .style-name { position: absolute; top: 346px; width: 300px; text-align: center; font-family: "Great Vibes", cursive; font-size: 30px; color: var(--ink); }

  /* Back-right panel */
  .flourish { position: absolute; left: 46px; top: 18px; width: 188px; height: 22px; background: var(--cream-deep); border-radius: 11px; }
  .story { position: absolute; left: 28px; top: 60px; width: 250px; font-size: 10.6px; line-height: 17.5px; letter-spacing: .2px; color: #2e2a2b; }
  .badge {
    position: absolute; width: 56px; height: 56px; border-radius: 50%;
    background: var(--brown); color: #fff; text-align: center;
  }
  .badge b { display: block; font-weight: 400; font-size: 21px; line-height: 22px; margin-top: 9px; }
  .badge span { display: block; font-size: 9px; line-height: 11px; }
  .badge.water b { font-size: 9.5px; font-weight: 500; line-height: 11px; margin-top: 5px; }
  .badge.water svg { display: block; margin: 2px auto 0; }
  .b1 { left: 33px; top: 188px; } .b2 { left: 109px; top: 188px; } .b3 { left: 185px; top: 188px; }
  .b4 { left: 68px; top: 257px; } .b5 { left: 148px; top: 257px; }
  .arrow-rule { position: absolute; left: 36px; top: 344px; }
  .social { position: absolute; left: 12px; top: 362px; width: 280px; display: flex; justify-content: space-between; font-size: 7.5px; font-weight: 500; }
  .social li { list-style: none; display: flex; align-items: center; gap: 3px; }
  .social .dot { width: 7px; height: 7px; border-radius: 50%; background: var(--ink); }
</style>
</head>
<body>
<section class="label">

  <div class="panel back-info">
    <div class="ingredients">
      <h2>INGREDIENTS</h2>
      <svg class="rule" width="166" height="6" viewBox="0 0 166 6">
        <line x1="4" y1="3" x2="162" y2="3" stroke="#fff" stroke-width="1"/>
        <circle cx="3" cy="3" r="2.2" fill="none" stroke="#fff"/>
        <circle cx="163" cy="3" r="2.2" fill="none" stroke="#fff"/>
      </svg>
      <p>woda, słód jęczmienny, chmiel,<br>liście limonki, drożdże</p>
    </div>

    <div class="facts">
      <div class="fact"><h3>BEST BEFORE:</h3><p>00/00/00</p></div>
      <div class="fact"><h3>VOLUME OF THE BOTTLE: :</h3><p>330ml</p></div>
      <div class="fact"><h3>VOLUME OF THE BOTTLE:</h3><p>Przechowywać w suchym i<br>ciemnym miejscu</p></div>
    </div>

    <div class="brewery">
      <div class="brewery-name">Warsztat Kominek <span class="mark"></span></div>
      <address>34-210 Sosnowa Dolina<br>Browar Pod Kamienną Turnią<br>Jaworzyna 48, 34-512 Jaworzyna</address>
    </div>
  </div>

  <div class="panel front">
    <div class="leaves top" role="img" aria-label="Line-drawn leaf cluster in the corner"></div>
    <div class="leaves side" role="img" aria-label="Line-drawn leaves along the edge"></div>
    <div class="sprig a" role="img" aria-label="Small dark herb sprig"></div>
    <div class="sprig b" role="img" aria-label="Small dark herb sprig"></div>
    <div class="sprig c" role="img" aria-label="Small dark herb sprig"></div>

    <h1 class="names">
      <span class="first">Julian</span>
      <span class="and">and</span>
      <span class="second">Alina</span>
    </h1>
    <p class="date">03.12.16</p>
    <div class="short-rule"></div>
    <p class="blurb">Lorem ipsum dolor sit amet, consectetur adipiscing elit, sed do eiusmod tempor incididunt ut labore et dolore magna aliqua.</p>
    <svg class="ornament-rule" width="216" height="6" viewBox="0 0 216 6">
      <line x1="3" y1="3" x2="213" y2="3" stroke="#d98a6c" stroke-width="1"/>
      <circle cx="3" cy="3" r="2" fill="none" stroke="#d98a6c"/>
      <circle cx="213" cy="3" r="2" fill="none" stroke="#d98a6c"/>
      <rect x="105" y="0.5" width="4" height="4" transform="rotate(45 107 2.5)" fill="#d98a6c"/>
    </svg>
    <p class="style-name">India Pale Ale</p>
  </div>

  <div class="panel back-story">
    <div class="flourish" role="img" aria-label="Swirled line flourish with a heart"></div>
    <p class="story">Trzymasz w ręku naszą autorską IPA do produkcji której wykorzystujemy wodę wypływającą z samego serca Beskidu Wysokiego – Babiej Góry. IPA lubi chmiele i goryczkę, ale żeby nie było nudno postanowiliśmy ją wzbogacić limonką.</p>

    <div class="badge b1"><b>ALK</b><span>5,5%</span></div>
    <div class="badge b2"><b>IBU</b><span>medium</span></div>
    <div class="badge b3"><b>EBC</b><span>Pale</span></div>
    <div class="badge b4"><b>EXT</b><span>14%</span></div>
    <div class="badge b5 water"><b>WATER</b>
      <svg width="20" height="26" viewBox="0 0 20 26">
        <path d="M10 1 C10 1 1 12 1 17 A9 9 0 0 0 19 17 C19 12 10 1 10 1Z" fill="#fff"/>
        <path d="M4 17 L8 12 L10 14 L12 11 L16 17 Z" fill="#6a3a30"/>
      </svg>
    </div>

    <svg class="arrow-rule" width="206" height="8" viewBox="0 0 206 8">
      <line x1="2" y1="4" x2="204" y2="4" stroke="#231f20" stroke-width="1"/>
      <path d="M0 4 L6 1 L6 7 Z M206 4 L200 1 L200 7 Z" fill="#231f20"/>
      <circle cx="22" cy="4" r="2.5" fill="#f3e4d9" stroke="#231f20"/>
      <circle cx="184" cy="4" r="2.5" fill="#f3e4d9" stroke="#231f20"/>
    </svg>

    <ul class="social">
      <li><span class="dot"></span>warsztatkominek</li>
      <li><span class="dot"></span>kominek.browar</li>
      <li><span class="dot"></span>www.warsztatkominek.pl</li>
    </ul>
  </div>

</section>
</body>
</html>
```